Stylish Business Cards Wanted

- DOUBLE SIDED Design Required -

High end, edgy cards for a corporate and personal stylist. Must include logo,
Name: Belinda Harwick
Title: Director and Stylist
telephone : +61 8 7142 5809
email: belinda@theloombriefing.example
website: theloombriefing.example
Tag: Corporate Workwear & Uniform Specialist | Personal Stylist
Would like nice icons for telephone, email, website

Target Market(s)

Businesses wanting stylish uniforms, people wanting stylish wardrobes

Industry/Entity Type

Corporate Workwear Stylist

Contact Information for Business Card

I would like black, white and gold foiling incorporated in the design - possibly a touch of the other colours on my branding guide attached Name: Belinda Harwick Title: Director and Stylist telephone : +61 8 7142 5809 email: belinda@theloombriefing.example website: theloombriefing.example Tag: Corporate Workwear & Uniform Specialist | Personal Stylist Would like nice icons for telephone, email, website

Font styles to use
Other font styles liked:
• Raleway

Colors

Designer to choose colors to be used in the design.

Requirements
Must have
• Gold foil accents

```html
<!DOCTYPE html>
<html lang="en">
<head>
<meta charset="utf-8">
<title>The Loom Briefing — Business Cards</title>
<link rel="stylesheet" href="https://fonts.googleapis.com/css2?family=Open+Sans:wght@400;700&display=swap">
<style>
  :root {
    --backdrop: #2a2a2a;
    --card: #161616;
    --gold: #d6cc8a;
    --gold-deep: #b9ad63;
  }
  * { box-sizing: border-box; margin: 0; padding: 0; }
  html, body {
    width: 1200px; height: 900px; overflow: hidden;
    background: var(--backdrop);
    font-family: "Open Sans", sans-serif;
    color: var(--gold);
  }
  .sheet {
    width: 1200px; height: 900px;
    display: flex; flex-direction: column; align-items: center; justify-content: center;
    gap: 56px;
  }
  .card {
    position: relative;
    width: 640px; height: 366px;
    background: var(--card);
    border-bottom: 3px solid var(--gold-deep);
    box-shadow: 0 14px 30px rgba(0,0,0,.45);
  }
  /* back side */
  .card--back { display: flex; align-items: center; justify-content: center; }
  .brand-name {
    font-weight: 700;
    color: var(--gold);
    letter-spacing: .06em;
    text-transform: uppercase;
    display: flex; align-items: center; gap: 14px;
  }
  .brand-name__dot {
    width: 14px; height: 14px; border-radius: 50%;
    background: var(--gold);
  }
  .card--back .brand-name { font-size: 40px; }
  /* front side */
  .card--front .brand-name {
    position: absolute; left: 40px; top: 118px;
    font-size: 22px; line-height: 1.2;
    width: 220px;
  }
  .divider {
    position: absolute; left: 290px; top: 60px;
    width: 1px; height: 190px;
    background: var(--gold-deep);
  }
  .contact {
    position: absolute; left: 320px; top: 74px;
  }
  .contact__name {
    font-weight: 700; font-size: 21px; letter-spacing: .03em;
    text-transform: uppercase;
  }
  .contact__title { font-size: 15px; margin-top: 2px; }
  .contact__list { list-style: none; margin-top: 26px; }
  .contact__item {
    display: flex; align-items: center; gap: 10px;
    font-size: 14.5px; line-height: 1.75;
  }
  .contact__icon { width: 14px; height: 14px; flex: none; }
  .tagline {
    position: absolute; left: 40px; bottom: 34px;
    font-size: 15px; letter-spacing: .01em;
  }
  .tagline__sep { margin: 0 10px; }
</style>
</head>
<body>
<main class="sheet">

  <section class="card card--back" aria-label="Card back">
    <div class="brand-name"><span class="brand-name__dot"></span>The Loom Briefing</div>
  </section>

  <section class="card card--front" aria-label="Card front">
    <div class="brand-name"><span class="brand-name__dot"></span><span>The Loom<br>Briefing</span></div>
    <div class="divider"></div>

    <div class="contact">
      <h1 class="contact__name">Belinda Harwick</h1>
      <p class="contact__title">Director and Stylist</p>
      <ul class="contact__list">
        <li class="contact__item">
          <svg class="contact__icon" viewBox="0 0 24 24" aria-hidden="true"><path fill="var(--gold)" d="M6.6 10.8a15.2 15.2 0 0 0 6.6 6.6l2.2-2.2c.3-.3.7-.4 1-.2 1.1.4 2.3.6 3.6.6.6 0 1 .4 1 1V20c0 .6-.4 1-1 1A17 17 0 0 1 3 4c0-.6.4-1 1-1h3.5c.6 0 1 .4 1 1 0 1.3.2 2.5.6 3.6.1.3 0 .7-.2 1z"/></svg>
          +61 8 7142 5809
        </li>
        <li class="contact__item">
          <svg class="contact__icon" viewBox="0 0 24 24" aria-hidden="true"><path fill="var(--gold)" d="M2 5h20v14H2z"/><path fill="none" stroke="var(--card)" stroke-width="2" d="M2.5 5.5 12 13l9.5-7.5"/></svg>
          belinda@theloombriefing.example
        </li>
        <li class="contact__item">
          <svg class="contact__icon" viewBox="0 0 24 24" aria-hidden="true"><g fill="none" stroke="var(--gold)" stroke-width="2"><circle cx="12" cy="12" r="9.5"/><ellipse cx="12" cy="12" rx="4" ry="9.5"/><path d="M2.5 12h19"/></g></svg>
          theloombriefing.example
        </li>
      </ul>
    </div>

    <p class="tagline">Corporate Workwear &amp; Uniform Specialist<span class="tagline__sep">•</span>Personal Stylist</p>
  </section>

</main>
</body>
</html>
```